Professional & attention grabbing.

A business card design, front and back. I already have a logo I will attach, but I am open to something new as well.
Things to include:
Name:
Title:
Phone:
Email:
Wanting something that is professional but attention grabbing.
Also we do a lot of work using drones on natural gas pipelines (leading the future)if you want to include any of that. I'm open to ideas.
Target Market(s)
Natural gas transmission industry / greenhouse gas mitigation industry
Industry/Entity Type
Business
Colors
Designer to choose colors to be used in the design.
Look and feel
Each slider illustrates characteristics of the customer's brand and the style your logo design should communicate.

```html
<!DOCTYPE html>
<html lang="en">
<head>
<meta charset="utf-8">
<title>Ridgeline Inspections – Business Card</title>
<link rel="stylesheet" href="https://fonts.googleapis.com/css2?family=Poppins:wght@400;500;700&display=swap">
<style>
  :root {
    --bg: #d9d9d9;
    --charcoal: #3a3a3d;
    --charcoal-dark: #2f2f31;
    --red: #c1202a;
    --white: #ffffff;
    --ink: #2b2b2d;
  }
  * { box-sizing: border-box; margin: 0; padding: 0; }
  html, body {
    width: 1200px; height: 1000px; overflow: hidden;
    background: var(--bg);
    font-family: "Poppins", sans-serif;
  }
  .sheet {
    position: relative; width: 1200px; height: 1000px;
    display: flex; align-items: center; justify-content: center; gap: 40px;
  }
  .card {
    position: relative; width: 540px; height: 310px;
    overflow: hidden;
    box-shadow: 0 6px 18px rgba(0,0,0,0.25);
  }
  .card-art { position: absolute; inset: 0; width: 100%; height: 100%; }

  /* Front */
  .card--front { background: var(--white); }
  .brand {
    position: absolute; display: flex; align-items: center; gap: 12px;
  }
  .brand-mark { width: 30px; height: 30px; background: var(--red); }
  .brand-name {
    font-weight: 700; font-size: 24px; letter-spacing: 0.5px;
    line-height: 1.05; text-transform: uppercase;
  }
  .card--front .brand { left: 34px; top: 34px; }
  .card--front .brand-name { color: var(--ink); }

  .person { position: absolute; left: 34px; top: 176px; }
  .person-name { color: var(--red); font-weight: 700; font-size: 20px; letter-spacing: 0.3px; }
  .person-title { color: var(--ink); font-weight: 500; font-size: 12px; margin-top: 2px; }

  .contact {
    position: absolute; right: 26px; bottom: 36px;
    list-style: none; color: var(--white); font-size: 14px; font-weight: 400;
  }
  .contact li { display: flex; align-items: center; justify-content: flex-end; gap: 8px; height: 24px; }
  .contact-icon { width: 16px; height: 16px; background: var(--red); display: flex; align-items: center; justify-content: center; border-radius: 2px; }
  .contact-icon svg { width: 11px; height: 11px; }

  /* Back */
  .card--back { background: var(--charcoal); display: flex; align-items: center; justify-content: center; }
  .card--back .brand { position: static; }
  .card--back .brand-mark { width: 40px; height: 40px; }
  .card--back .brand-name { color: var(--white); font-size: 30px; }
</style>
</head>
<body>
<main class="sheet">
  <section class="card card--front" aria-label="Card front">
    <svg class="card-art" viewBox="0 0 540 310" preserveAspectRatio="none" aria-hidden="true">
      <path fill="var(--red)" d="M0,248 C120,248 260,212 390,150 C270,228 130,264 0,272 Z"/>
      <path fill="var(--charcoal)" d="M540,0 C470,110 300,250 0,282 L0,310 L540,310 Z"/>
    </svg>
    <div class="brand">
      <span class="brand-mark"></span>
      <span class="brand-name">Ridgeline<br>Inspections</span>
    </div>
    <div class="person">
      <p class="person-name">DANIEL REYES</p>
      <p class="person-title">FOUNDER</p>
    </div>
    <ul class="contact">
      <li>000 000 0000
        <span class="contact-icon"><svg viewBox="0 0 24 24" fill="#fff"><path d="M6.6 10.8a15.1 15.1 0 0 0 6.6 6.6l2.2-2.2a1 1 0 0 1 1-.25 11.4 11.4 0 0 0 3.6.57 1 1 0 0 1 1 1V20a1 1 0 0 1-1 1A17 17 0 0 1 3 4a1 1 0 0 1 1-1h3.5a1 1 0 0 1 1 1c0 1.25.2 2.45.57 3.57a1 1 0 0 1-.25 1z"/></svg></span>
      </li>
      <li>info@yourmail.com
        <span class="contact-icon"><svg viewBox="0 0 24 24" fill="none" stroke="#fff" stroke-width="2"><rect x="3" y="5" width="18" height="14"/><path d="M3 5l9 8 9-8"/></svg></span>
      </li>
    </ul>
  </section>

  <section class="card card--back" aria-label="Card back">
    <div class="brand">
      <span class="brand-mark"></span>
      <span class="brand-name">Ridgeline<br>Inspections</span>
    </div>
  </section>
</main>
</body>
</html>
```